Real Estate Business Card

On the front side I want to have my info, my brokerage info.
On the back side I want have my complany’s logo, website and Facebook link. I will provide all this once I select a design.

I would like to see Black background and gold text, Dark Blue and gold text and White and blue text designs

Font styles to use
Sans Serif
Script

```html
<!DOCTYPE html>
<html lang="en">
<head>
<meta charset="utf-8">
<title>Trueward Real Estate – Business Card</title>
<link rel="stylesheet" href="https://fonts.googleapis.com/css2?family=Montserrat:wght@800&family=Roboto:wght@400;500;700&display=swap">
<style>
  :root {
    --backdrop: #2b2b2d;
    --card: #1e1e20;
    --brand-red: #d8262e;
    --brand-slate: #8c93a6;
    --gold: #f2dc85;
    --text-light: #f4f4f4;
  }
  * { box-sizing: border-box; margin: 0; padding: 0; }
  html, body {
    width: 1200px; height: 900px; overflow: hidden;
    background: var(--backdrop);
  }
  .stage { position: relative; width: 1200px; height: 900px; }

  .card {
    position: absolute;
    width: 620px; height: 340px;
    background: var(--card);
    border-radius: 4px;
    box-shadow: 0 10px 30px rgba(0,0,0,.45);
  }
  .card--back { left: 290px; top: 70px; }
  .card--front { left: 290px; top: 470px; }

  /* wordmark */
  .wordmark {
    display: flex; flex-direction: column; align-items: center;
    font-family: "Montserrat", sans-serif; font-weight: 800;
    color: var(--brand-slate); line-height: 1;
  }
  .wordmark__name { font-size: 52px; letter-spacing: 1px; }
  .wordmark__tagline { font-size: 13px; letter-spacing: 9px; margin-top: 8px; padding-left: 9px; }
  .wordmark__square {
    width: 42px; height: 42px; background: var(--brand-red); margin-bottom: 16px;
  }

  .card--back .wordmark { position: absolute; left: 0; right: 0; top: 70px; }
  .website {
    position: absolute; left: 0; right: 0; top: 262px;
    text-align: center;
    font-family: "Roboto", sans-serif; font-weight: 500; font-size: 15px;
    letter-spacing: 8px; color: var(--text-light);
  }

  /* front */
  .brand-block {
    position: absolute; left: 40px; top: 50px;
    width: 240px; height: 240px;
    background: var(--brand-red);
  }
  .card--front .wordmark {
    position: absolute; right: 34px; top: 34px; align-items: flex-end;
  }
  .card--front .wordmark__name { font-size: 40px; }
  .card--front .wordmark__tagline { font-size: 11px; letter-spacing: 7px; }

  .contact {
    position: absolute; right: 34px; top: 150px;
    text-align: right;
    font-family: "Roboto", sans-serif; color: var(--text-light);
  }
  .contact__name { font-size: 25px; font-weight: 700; color: var(--gold); letter-spacing: .5px; }
  .contact__role { font-size: 16px; font-weight: 500; color: var(--brand-red); margin-bottom: 10px; }
  .contact__line { font-size: 17px; line-height: 1.35; }
  .contact__label { color: var(--gold); font-weight: 700; }
</style>
</head>
<body>
<main class="stage">
  <section class="card card--back" aria-label="Card back">
    <div class="wordmark">
      <span class="wordmark__square"></span>
      <span class="wordmark__name">TRUEWARD</span>
      <span class="wordmark__tagline">REAL ESTATE</span>
    </div>
    <p class="website">www.trueward.com</p>
  </section>

  <section class="card card--front" aria-label="Card front">
    <div class="brand-block" role="img" aria-label="Brand colour block"></div>
    <div class="wordmark">
      <span class="wordmark__name">TRUEWARD</span>
      <span class="wordmark__tagline">REAL ESTATE</span>
    </div>
    <div class="contact">
      <p class="contact__name">DANA WHITLOCK</p>
      <p class="contact__role">CEO/FOUNDER</p>
      <p class="contact__line">4120 Alder Crest Road</p>
      <p class="contact__line">Juneau, Alaska 99801</p>
      <p class="contact__line"><span class="contact__label">P:</span> 555 014 2738</p>
      <p class="contact__line"><span class="contact__label">M:</span> 555 019 4460</p>
      <p class="contact__line"><span class="contact__label">E:</span> dana@trueward.com</p>
    </div>
  </section>
</main>
</body>
</html>
```